Stationery Design Project for Nimbora, Chicago

Nimbora, a street parking application which helps car drivers find a street parking spot by offering an ideal path along which to look for parking. This path is calculated by our algorithm based on data (e.g. historical data, baseball games schedule, etc.). Along this path the driver will find a spot and will also save 70% of the search time. Customer we target is reg. between 21 and 45 yo.

We envision something young, fresh, bright and original. Slightly abstract maybe. It should represent the idea and elements of finding street parking in the city, e.g. car(s), parking spot, people, city, etc. (just ideas!).

Logo is attached.

Requirement:
- Business Cards (2 Sided Full Color CMYK)
- Letterhead (1 Sided Full Color CMYK)
- Envelope (1 Sided Full Color CMYK)
- Sticker (1 Sided Full Color CMYK), round with a 2inch diameter.

Reason: We're starting to get more and more designs and need more time to look into all of them. Very exciting!! Thanks to everybody!

Hi all, we're in the process of selecting our favs. Though choices!!! Really good submissions. Will keep you posted and sorry for the delay.

Target Market(s)

Car drivers and owners between 21 and 45

Industry/Entity Type

Parking

Requirements
Must have
• Sticker should be round and include company URL nimbora.com and the new logo which we will attach soon.
Should not have
• Should not be too serious or boring.

```html
<!DOCTYPE html>
<html lang="en">
<head>
<meta charset="utf-8">
<title>Nimbora Business Card</title>
<link rel="stylesheet" href="https://fonts.googleapis.com/css2?family=Open+Sans:wght@400;600;700&display=swap">
<style>
  :root {
    --backdrop: #e9e6e2;
    --card: #ffffff;
    --card-edge: #c9c4bd;
    --ink: #1e1e1e;
    --ink-soft: #333333;
    --brand-blue: #1f4fd1;
    --road-blue: #8ea6d8;
  }
  * { margin: 0; padding: 0; box-sizing: border-box; }
  html, body {
    width: 1200px; height: 1044px; overflow: hidden;
    background: var(--backdrop);
    font-family: "Open Sans", Arial, sans-serif;
    color: var(--ink);
  }
  .canvas { position: relative; width: 1200px; height: 1044px; }
  .card {
    position: absolute;
    width: 736px; height: 419px;
    background: var(--card);
    border: 1px solid var(--card-edge);
    box-shadow: 0 2px 6px rgba(0,0,0,0.12);
    overflow: hidden;
  }
  .card--front { left: 73px; top: 77px; }
  .card--back { left: 363px; top: 540px; }

  .brand { position: absolute; display: flex; align-items: center; gap: 22px; }
  .brand__dot {
    width: 98px; height: 98px; border-radius: 50%;
    background: var(--brand-blue);
    flex: none;
  }
  .brand__name {
    font-size: 58px; font-weight: 600; color: var(--ink-soft);
    letter-spacing: -0.5px; line-height: 1;
  }
  .card--front .brand { left: 39px; top: 38px; }
  .card--back .brand { left: 144px; top: 147px; }

  .feature-graphic {
    position: absolute; left: 396px; top: 0; width: 315px; height: 419px;
    background: linear-gradient(180deg, rgba(142,166,216,0.15) 0%, rgba(142,166,216,0.55) 100%);
  }

  .holder { position: absolute; left: 46px; top: 190px; font-size: 22px; }
  .holder__name { font-weight: 700; }
  .holder__title { font-size: 17px; font-weight: 400; }

  .contacts { position: absolute; left: 46px; top: 242px; list-style: none; font-size: 18px; color: var(--ink-soft); }
  .contacts li { display: flex; align-items: center; height: 27px; }
  .contacts svg { width: 14px; height: 14px; margin-right: 10px; fill: var(--ink-soft); }

  .address { position: absolute; left: 46px; top: 366px; font-size: 18px; color: var(--ink-soft); }

  .web { position: absolute; left: 0; width: 100%; top: 316px; text-align: center; font-size: 22px; letter-spacing: 2px; color: var(--ink-soft); }
</style>
</head>
<body>
<div class="canvas">

  <section class="card card--front">
    <div class="brand">
      <span class="brand__dot"></span>
      <span class="brand__name">Nimbora</span>
    </div>

    <div class="feature-graphic" role="img" aria-label="Brand graphic area: a winding blue road rising into an arrow through pale parking bays"></div>

    <p class="holder"><span class="holder__name">Your Name ,</span> <span class="holder__title">Title</span></p>

    <ul class="contacts">
      <li><svg viewBox="0 0 14 14"><path d="M3 1l2 3-1.2 1.3a8 8 0 0 0 4.9 4.9L10 9l3 2-1.5 2C6 13 1 8 1 2.5z"/></svg>+91 12345 67890</li>
      <li><svg viewBox="0 0 14 14"><path d="M4 0h6a1 1 0 0 1 1 1v12a1 1 0 0 1-1 1H4a1 1 0 0 1-1-1V1a1 1 0 0 1 1-1zm1 2v7h4V2zm2 9a1 1 0 1 0 0 2 1 1 0 0 0 0-2z"/></svg>+91 12345 67890</li>
      <li><svg viewBox="0 0 14 14"><path d="M1 3h12v9H1zm1 1v.6l5 3.4 5-3.4V4z"/></svg>info@nimbora.com</li>
      <li><svg viewBox="0 0 14 14"><circle cx="7" cy="7" r="6"/></svg>www.nimbora.com</li>
    </ul>

    <p class="address">Complex Name, Street Name, Area, City Name,000 000</p>
  </section>

  <section class="card card--back">
    <div class="brand">
      <span class="brand__dot"></span>
      <span class="brand__name">Nimbora</span>
    </div>
    <p class="web">www.nimbora.com</p>
  </section>

</div>
</body>
</html>
```